Business Card Design For Office Furniture Clearance Company

Kestrel Office Clearance - our company name pretty much explains what we do, we clear offices for high end clients, mainly plc's and large international companies.

We require a nice looking business card that displays professionalism but without being too serious.

It would be nice to see just a little more than a conventional boring business card, make sure you add some flare.

Industry/Entity Type

Office Furniture

Contact Information for Business Card

CARD 1

Mark Holloway
Director
mark@kestrelofficeclearance.co.uk
m: 07700 153928

t: 01632 960418
www.kestrelofficeclearance.co.uk

Kestrel Office Clearance
Unit K4 B
2-8 Fenwick Lane
Harwick
Stonebury
ZZ9 4QT

Free office clearances… no better deal anywhere.

CARD 2

Peter Radford
Director
peter@kestrelofficeclearance.co.uk
m: 07700 382615

t: 01632 960418

Kestrel Office Clearance
Unit K4 B
2-8 Fenwick Lane
Harwick
Stonebury
ZZ9 4QT

Font styles to use
Sans Serif

Requirements
Must have
• A white background - as we have a blue logo.
Nice to have
• Nice use of the logo - play around with this and dissect it.

```html
<!DOCTYPE html>
<html lang="en">
<head>
<meta charset="utf-8">
<title>Kestrel Office Clearance – Business Card</title>
<link href="https://fonts.googleapis.com/css2?family=Montserrat:wght@500;600;700&display=swap" rel="stylesheet">
<style>
  :root {
    --backdrop: #2b2b2d;
    --card: #ffffff;
    --brand-blue: #1b7ec2;
    --deep-blue: #15609a;
    --flame-warm: rgba(250, 214, 170, 0.45);
    --flame-soft: rgba(252, 236, 214, 0.25);
  }
  * { margin: 0; padding: 0; box-sizing: border-box; }
  html, body {
    width: 1200px; height: 900px; overflow: hidden;
    background: var(--backdrop);
    font-family: "Montserrat", sans-serif;
  }
  .canvas { position: relative; width: 1200px; height: 900px; }
  .card {
    position: absolute; left: 250px;
    width: 700px; height: 400px;
    background: var(--card);
    border-radius: 30px;
    overflow: hidden;
  }
  .card--brand { top: 35px; }
  .card--contact { top: 465px; }

  /* brand side */
  .brand-block {
    position: absolute; right: 50px; top: 95px;
    display: flex; flex-direction: column; align-items: flex-end;
  }
  .brand-disc {
    width: 150px; height: 150px; border-radius: 50%;
    background: var(--brand-blue);
    margin-right: 70px; margin-bottom: 14px;
  }
  .brand-name {
    color: var(--brand-blue); font-weight: 700; font-size: 24px;
    text-transform: uppercase; letter-spacing: 0.2px; white-space: nowrap;
  }
  .brand-url {
    color: var(--deep-blue); font-weight: 600; font-size: 15px;
    margin-top: 6px; white-space: nowrap;
  }

  /* contact side */
  .flame-art {
    position: absolute; right: 20px; top: 20px;
    width: 330px; height: 300px;
    background: radial-gradient(ellipse at 50% 55%, var(--flame-warm), var(--flame-soft) 55%, transparent 75%);
  }
  .mark-block {
    position: absolute; right: 70px; top: 70px;
    display: flex; flex-direction: column; align-items: center;
  }
  .mark-disc {
    width: 170px; height: 170px; border-radius: 50%;
    background: var(--brand-blue);
  }
  .mark-name {
    margin-top: 12px; color: var(--brand-blue);
    font-weight: 700; font-size: 15px; text-transform: uppercase; white-space: nowrap;
  }
  .contact {
    position: absolute; left: 38px; top: 95px;
    color: var(--brand-blue);
  }
  .contact__name {
    font-weight: 700; font-size: 26px; text-transform: uppercase;
    color: var(--deep-blue); line-height: 1;
  }
  .contact__role {
    font-weight: 600; font-size: 13px; text-transform: uppercase;
    margin-top: 4px;
  }
  .contact__address {
    font-weight: 600; font-size: 15px; line-height: 1.35;
    margin-top: 14px; color: var(--deep-blue);
  }
  .contact__list { list-style: none; margin-top: 12px; }
  .contact__item {
    display: flex; align-items: center; gap: 10px;
    font-weight: 600; font-size: 16px; line-height: 1.5;
    color: var(--deep-blue); white-space: nowrap;
  }
  .contact__icon { width: 14px; height: 14px; flex: none; }
  .tagline {
    position: absolute; left: 38px; bottom: 32px;
    color: var(--brand-blue); font-weight: 600; font-size: 20px;
    text-transform: uppercase; letter-spacing: 0.2px; white-space: nowrap;
  }
</style>
</head>
<body>
<main class="canvas">

  <section class="card card--brand">
    <div class="brand-block">
      <div class="brand-disc"></div>
      <div class="brand-name">Kestrel Office Clearance</div>
      <div class="brand-url">www.kestrelofficeclearance.co.uk</div>
    </div>
  </section>

  <section class="card card--contact">
    <div class="flame-art" role="img" aria-label="Faint warm flame illustration behind the brand mark"></div>
    <div class="mark-block">
      <div class="mark-disc"></div>
      <div class="mark-name">Kestrel Office Clearance</div>
    </div>

    <div class="contact">
      <div class="contact__name">Mark Holloway</div>
      <div class="contact__role">Director</div>
      <div class="contact__address">Unit K4 B, 2-8 Fenwick Lane, Harwick,<br>Stonebury, ZZ9 4QT</div>
      <ul class="contact__list">
        <li class="contact__item">
          <svg class="contact__icon" viewBox="0 0 14 14"><rect x="3.5" y="1" width="7" height="12" rx="1.5" fill="none" stroke="var(--deep-blue)" stroke-width="1.5"/><circle cx="7" cy="10.8" r="0.8" fill="var(--deep-blue)"/></svg>
          07700 153928
        </li>
        <li class="contact__item">
          <svg class="contact__icon" viewBox="0 0 14 14"><path d="M3 1.5l2.3 2.6-1.2 1.6c.8 1.8 2.3 3.3 4.1 4.1l1.6-1.2 2.6 2.3-1.4 1.6C6 12.3 1.7 8 1.4 2.9z" fill="var(--deep-blue)"/></svg>
          01632 960418
        </li>
        <li class="contact__item">
          <svg class="contact__icon" viewBox="0 0 14 14"><rect x="1" y="3" width="12" height="8.5" rx="1" fill="none" stroke="var(--deep-blue)" stroke-width="1.4"/><path d="M1.5 3.6L7 8l5.5-4.4" fill="none" stroke="var(--deep-blue)" stroke-width="1.4"/></svg>
          mark@kestrelofficeclearance.co.uk
        </li>
        <li class="contact__item">
          <svg class="contact__icon" viewBox="0 0 14 14"><circle cx="7" cy="7" r="5.8" fill="none" stroke="var(--deep-blue)" stroke-width="1.3"/><ellipse cx="7" cy="7" rx="2.5" ry="5.8" fill="none" stroke="var(--deep-blue)" stroke-width="1.1"/><path d="M1.2 7h11.6" stroke="var(--deep-blue)" stroke-width="1.1"/></svg>
          www.kestrelofficeclearance.co.uk
        </li>
      </ul>
    </div>

    <div class="tagline">Free office clearances… no better deal anywhere</div>
  </section>

</main>
</body>
</html>
```